Commercial Refrigeration Service Company requires stylish and fresh looking flyer.

We need a flyer to hand out to new customers. It should have a photo and our branding, list all the services that are offered and our contact details.
We would like two flyers to be supplied, both identical though one offering a discount until July ( Half Price Service Fee ). The flyer should be clear, interesting and in similar colours to the branding package supplied.
Please look at our website for information about the services on offer:
www.brisko-coolworks.com.au

Target Market(s)

Cafes, bars, restaurants, pubs ect.

Font styles to use
Other font styles liked:
• Font package provided

Colors
85cae6
ffffff
333333

Requirements
Must have
• - The photo provided.
• - The company logo.
• - Similar feel to the website & business card.
• - Smooth layout and clear to understand.
Should not have
• - No clunky badges or prints.

```html
<!DOCTYPE html>
<html lang="en">
<head>
<meta charset="utf-8">
<title>Brisko Commercial Refrigeration Flyer</title>
<link rel="stylesheet" href="https://fonts.googleapis.com/css2?family=Bebas+Neue&family=Raleway:wght@300;400;600;700&display=swap">
<style>
  :root {
    --brand-blue: #5bc2ea;
    --brand-blue-soft: #85cae6;
    --ink: #2d2d2d;
    --charcoal: #333333;
    --paper: #f3f3f3;
    --paper-low: #e4e4e4;
    --icon-grey: #8a8a8a;
    --white: #ffffff;
    --backdrop: #e9e9e9;
  }
  * { box-sizing: border-box; margin: 0; padding: 0; }
  html, body { width: 1200px; height: 1146px; overflow: hidden; }
  body {
    background: var(--backdrop); position: relative;
    font-family: "Raleway", sans-serif; font-variant-numeric: lining-nums;
  }

  .flyer {
    position: absolute; left: 223px; top: 40px;
    width: 753px; height: 1066px; overflow: hidden;
    background: linear-gradient(180deg, var(--paper) 0%, var(--paper-low) 100%);
  }
  .hero-photo {
    position: absolute; left: 0; top: 0; width: 753px; height: 300px;
    background: linear-gradient(180deg, #9cc0de 0%, #c9d6df 38%, #7f8790 62%, #55595f 100%);
  }
  .brand-band {
    position: absolute; left: 0; top: 300px; width: 753px; height: 152px;
    background: var(--brand-blue);
    display: flex; align-items: center; justify-content: center;
  }
  .brand-name {
    font-family: "Raleway", sans-serif; font-weight: 600;
    font-size: 52px; letter-spacing: 0.06em;
    color: var(--ink);
  }
  .business-line {
    position: absolute; left: 0; right: 0; top: 486px; text-align: center;
    font-weight: 400; font-size: 22px; letter-spacing: 0.06em; color: var(--ink);
  }
  .services-title {
    position: absolute; left: 0; right: 0; top: 554px;
    display: flex; justify-content: center; align-items: center; gap: 6px;
    font-family: "Raleway", sans-serif; font-weight: 700; font-size: 21px;
    color: var(--brand-blue);
  }
  .services-title::before, .services-title::after {
    content: ""; width: 62px; height: 2px; background: var(--brand-blue);
  }
  .service {
    position: absolute; width: 220px; margin-left: -110px;
    display: flex; flex-direction: column; align-items: center;
  }
  .service svg { width: 70px; height: 70px; }
  .service-label {
    margin-top: 8px; font-family: "Bebas Neue", sans-serif;
    font-size: 23px; color: var(--brand-blue); white-space: nowrap;
  }
  .footer {
    position: absolute; left: 0; top: 866px; width: 753px; height: 200px;
    background: var(--ink); border-top: 4px solid var(--brand-blue);
  }
  .footer-notch { position: absolute; left: 355px; top: -4px; width: 44px; height: 36px; }
  .web-address {
    position: absolute; left: 0; right: 0; top: 43px; text-align: center;
    font-weight: 700; font-size: 18px; letter-spacing: 0.17em; color: var(--brand-blue);
  }
  .contact-lines {
    position: absolute; left: 0; right: 0; top: 74px; text-align: center;
    font-weight: 300; font-size: 17px; line-height: 20px; color: var(--white);
  }
  .social-row {
    position: absolute; left: 0; right: 0; top: 152px;
    display: flex; justify-content: center; align-items: center; gap: 3px;
  }
  .social-row .rule { width: 34px; height: 2px; background: var(--brand-blue); margin: 0 4px; }
  .social-row .dot { width: 22px; height: 22px; border-radius: 50%; background: var(--white); }
</style>
</head>
<body>
<main class="flyer">
  <div class="hero-photo" role="img" aria-label="Photo of the technician leaning on the branded service ute parked by the beach"></div>

  <section class="brand-band">
    <div class="brand-name">BRISKO</div>
  </section>

  <div class="business-line">COMMERCIAL REFRIGERATION</div>

  <h2 class="services-title">OUR SERVICES</h2>

  <div class="service" style="left:175px; top:606px;">
    <svg viewBox="0 0 70 70"><rect x="14" y="14" width="42" height="42" transform="rotate(45 35 35)" fill="var(--icon-grey)" stroke="var(--brand-blue)" stroke-width="3"/>
      <g fill="none" stroke="#fff" stroke-width="1.6"><path d="M32 22v18a5 5 0 1 0 6 0V22a3 3 0 0 0-6 0z"/><path d="M41 25h4M41 29h3M41 33h4"/></g></svg>
    <span class="service-label">COMMERCIAL REFRIGERATION</span>
  </div>
  <div class="service" style="left:345px; top:606px;">
    <svg viewBox="0 0 70 70"><rect x="14" y="14" width="42" height="42" transform="rotate(45 35 35)" fill="var(--icon-grey)" stroke="var(--brand-blue)" stroke-width="3"/>
      <g fill="none" stroke="#fff" stroke-width="1.6"><path d="M25 24h20l-3 22H28z"/><rect x="30" y="31" width="5" height="5"/><rect x="36" y="36" width="5" height="5"/></g></svg>
    <span class="service-label">ICE MAKERS</span>
  </div>
  <div class="service" style="left:480px; top:606px;">
    <svg viewBox="0 0 70 70"><rect x="14" y="14" width="42" height="42" transform="rotate(45 35 35)" fill="var(--icon-grey)" stroke="var(--brand-blue)" stroke-width="3"/>
      <g fill="none" stroke="#fff" stroke-width="1.6"><path d="M38 20l-6 12"/><path d="M26 32h14v6H26z"/><path d="M36 38v6"/><circle cx="36" cy="47" r="2"/></g></svg>
    <span class="service-label">BEER SYSTEMS</span>
  </div>
  <div class="service" style="left:608px; top:606px;">
    <svg viewBox="0 0 70 70"><rect x="14" y="14" width="42" height="42" transform="rotate(45 35 35)" fill="var(--icon-grey)" stroke="var(--brand-blue)" stroke-width="3"/>
      <path d="M38 21L29 37h6l-3 13 10-17h-6z" fill="none" stroke="#fff" stroke-width="1.6"/></svg>
    <span class="service-label">ELECTRICAL</span>
  </div>

  <div class="service" style="left:234px; top:723px;">
    <svg viewBox="0 0 70 70"><rect x="14" y="14" width="42" height="42" transform="rotate(45 35 35)" fill="var(--icon-grey)" stroke="var(--brand-blue)" stroke-width="3"/>
      <g fill="none" stroke="#fff" stroke-width="1.6"><path d="M24 24l22 22M24 24l3-1 1 3"/><path d="M46 24L24 46"/><circle cx="44" cy="26" r="3"/></g></svg>
    <span class="service-label">24HR SERVICE</span>
  </div>
  <div class="service" style="left:359px; top:723px;">
    <svg viewBox="0 0 70 70"><rect x="14" y="14" width="42" height="42" transform="rotate(45 35 35)" fill="var(--icon-grey)" stroke="var(--brand-blue)" stroke-width="3"/>
      <g fill="none" stroke="#fff" stroke-width="1.6"><path d="M22 27h5l3 12h14l3-9H28"/><circle cx="31" cy="43" r="2"/><circle cx="42" cy="43" r="2"/></g></svg>
    <span class="service-label">SALES</span>
  </div>
  <div class="service" style="left:487px; top:723px;">
    <svg viewBox="0 0 70 70"><rect x="14" y="14" width="42" height="42" transform="rotate(45 35 35)" fill="var(--icon-grey)" stroke="var(--brand-blue)" stroke-width="3"/>
      <g fill="none" stroke="#fff" stroke-width="1.6"><path d="M26 44l16-18 3 3-16 18-4 1z"/><path d="M26 26l18 18"/></g></svg>
    <span class="service-label">INSTALLATION</span>
  </div>

  <footer class="footer">
    <svg class="footer-notch" viewBox="0 0 44 36"><path d="M0 0h44L22 32z" fill="var(--brand-blue)"/><path d="M5 0h34L22 25z" fill="var(--paper-low)"/></svg>
    <div class="web-address">WWW.BRISKO-COOLWORKS.COM.AU</div>
    <div class="contact-lines">
      PO Box 1187 Seacliff NSW 2099<br>
      0412 555 018 &nbsp;|&nbsp; info@brisko-coolworks.com.au<br>
      ABN: 41 208 735 912 &nbsp;|&nbsp; Licence No: 418235B
    </div>
    <div class="social-row">
      <span class="rule"></span>
      <span class="dot"></span><span class="dot"></span><span class="dot"></span>
      <span class="rule"></span>
    </div>
  </footer>
</main>
</body>
</html>
```